i need a business card design for my family investment company "quorin investments" based in dubai. its a diverse investment firm focusing on education, hospitality and automotive. the design has to be modern and try to incorporate the logo "E" in the design. details on card as follow

Yusuf K Bin Tarrah
Managing Director
yusuf@quorin-mail.ae
www.quorin-mail.ae

Harbor district,palwick tower, office 1708, dubai
tel. 04 3850927
mobile.050 9184203

card used for networking events and investor meetings

Hospitality

```html
<!DOCTYPE html>
<html lang="en">
<head>
<meta charset="utf-8">
<title>Quorin Investments – Business Card</title>
<link rel="stylesheet" href="https://fonts.googleapis.com/css2?family=Lato:wght@300;400;700&display=swap">
<style>
  :root {
    --backdrop: #dcdcdc;
    --card-black: #050505;
    --card-white: #ffffff;
    --steel-blue: #4c78a8;
    --ink-white: #f2f2f2;
    --ink-black: #111111;
    --divider: #6b6b6b;
  }
  * { box-sizing: border-box; margin: 0; padding: 0; }
  html, body { width: 1200px; height: 926px; overflow: hidden; }
  body {
    background: var(--backdrop);
    font-family: "Lato", Arial, sans-serif;
    display: flex;
    flex-direction: column;
    align-items: center;
    justify-content: center;
    gap: 40px;
  }
  .card {
    width: 700px;
    height: 400px;
    position: relative;
    overflow: hidden;
    box-shadow: 0 6px 18px rgba(0,0,0,0.18);
  }

  /* Shared wordmark */
  .wordmark {
    display: flex;
    align-items: center;
    justify-content: center;
    gap: 18px;
    white-space: nowrap;
    font-weight: 300;
    text-transform: uppercase;
  }
  .wordmark-square {
    width: 22px;
    height: 22px;
    background: var(--steel-blue);
    flex: none;
  }
  .wordmark-name {
    font-size: 30px;
    letter-spacing: 10px;
    line-height: 1;
  }

  /* Front side */
  .card-front { background: var(--card-black); }
  .front-head {
    height: 178px;
    background: var(--card-white);
    display: flex;
    align-items: center;
    justify-content: center;
  }
  .front-head .wordmark-name { color: var(--ink-black); }
  .front-body {
    padding-top: 22px;
    text-align: center;
    color: var(--ink-white);
  }
  .holder-name {
    color: var(--steel-blue);
    font-size: 30px;
    font-weight: 400;
    line-height: 1.1;
  }
  .holder-name b { font-weight: 700; }
  .holder-title {
    font-size: 19px;
    font-weight: 300;
    letter-spacing: 2px;
    margin-top: 2px;
  }
  .contact-grid {
    display: grid;
    grid-template-columns: 1fr 28px 1fr;
    margin: 18px auto 0;
    width: 620px;
    font-size: 16px;
    row-gap: 4px;
  }
  .contact-col-left { text-align: right; }
  .contact-col-right { text-align: left; }
  .contact-divider {
    justify-self: center;
    width: 1px;
    background: var(--divider);
    margin: 3px 0;
  }
  .contact-label { color: var(--steel-blue); }
  .address {
    margin-top: 18px;
    font-size: 19px;
    font-weight: 700;
    letter-spacing: 2.5px;
    text-transform: uppercase;
    white-space: nowrap;
  }

  /* Back side */
  .card-back {
    background: var(--card-black);
    display: flex;
    align-items: center;
    justify-content: center;
  }
  .card-back .wordmark-name { color: var(--ink-white); }
</style>
</head>
<body>

  <section class="card card-front" aria-label="Business card front">
    <header class="front-head">
      <div class="wordmark">
        <span class="wordmark-square"></span>
        <span class="wordmark-name">Quorin Investments</span>
      </div>
    </header>
    <div class="front-body">
      <h1 class="holder-name">Yusuf <b>K Bin Tarrah</b></h1>
      <p class="holder-title">managing director</p>
      <div class="contact-grid">
        <div class="contact-col-left">
          <p><span class="contact-label">tel.</span> 04 3850927</p>
          <p><span class="contact-label">web.</span> www.quorin-mail.ae</p>
        </div>
        <span class="contact-divider"></span>
        <div class="contact-col-right">
          <p><span class="contact-label">mobile.</span> 050 9184203</p>
          <p><span class="contact-label">email.</span> yusuf@quorin-mail.ae</p>
        </div>
      </div>
      <p class="address">Harbor District, Palwick Tower, Office 1708, Dubai</p>
    </div>
  </section>

  <section class="card card-back" aria-label="Business card back">
    <div class="wordmark">
      <span class="wordmark-square"></span>
      <span class="wordmark-name">Quorin Investments</span>
    </div>
  </section>

</body>
</html>
```